Dorwin's Coating & Renewal Letterhead Design We want to revamp out old traditional letterhead with the new logo designs that are attached. We are working on getting all our company items from vehicles, business, cards, t-shirts, letterhead to match. This should include company colors, fonts, and flow of items that we have attached below.

Industry/Entity Type

Construction Company

Font styles to use
Sans Serif
Other font styles liked:
• Bold with outline

Colors
ec1f27
ffffff

Requirements
Must have
• Company Name: Dorwin's Coating & Renewal
• Address: 4728 SW 81st Ter Halverd cove fl 39417
• Office Number: (555) 413-2986
• Email: Dorwinrenewal@mailbrook.example
• License Number: KRT8046392
Nice to have
• Company Colors: red, white, black, and grey

```html
<!DOCTYPE html>
<html lang="en">
<head>
<meta charset="utf-8">
<title>Dorwin's Coating &amp; Renewal – Letterhead</title>
<link href="https://fonts.googleapis.com/css2?family=Arimo:wght@400;700&family=Archivo+Black&display=swap" rel="stylesheet">
<style>
  :root {
    --brand-red: #ec1f27;
    --ink-black: #1a1a1a;
    --ink-grey: #7a7a7a;
    --soft-grey: #c9c9c9;
    --pale-grey: #e6e6e6;
    --paper: #ffffff;
    --backdrop: #dfe1e3;
  }
  * { box-sizing: border-box; margin: 0; padding: 0; }
  html, body {
    width: 1200px; height: 784px; overflow: hidden;
    background: var(--backdrop);
    font-family: "Arimo", Arial, sans-serif;
  }
  .letterhead {
    position: absolute; left: 338px; top: 22px;
    width: 524px; height: 740px;
    background: var(--paper);
    box-shadow: 0 2px 10px rgba(0,0,0,.12);
    overflow: hidden;
  }
  .corner { position: absolute; width: 150px; height: 96px; }
  .corner--top { top: 0; right: 0; }
  .corner--bottom { bottom: 0; left: 0; transform: rotate(180deg); }

  .masthead {
    position: absolute; top: 80px; right: 22px;
    display: flex; align-items: center; gap: 12px;
  }
  .brand-name {
    font-family: "Archivo Black", "Arimo", sans-serif;
    font-size: 15px; line-height: 1.1;
    color: var(--brand-red);
    text-align: right; width: 120px;
  }
  .contact {
    border-left: 1px solid var(--soft-grey);
    padding-left: 10px;
    list-style: none;
    font-size: 7px; line-height: 1.45;
    color: var(--ink-grey);
  }
  .contact li { display: flex; gap: 5px; align-items: flex-start; white-space: nowrap; }
  .contact svg { flex: none; width: 7px; height: 7px; margin-top: 1px; }
  .contact .address { color: var(--brand-red); font-weight: 700; }

  .letter-body {
    position: absolute; top: 166px; left: 56px; width: 384px;
    font-size: 9.5px; line-height: 1.55; color: var(--ink-grey);
  }
  .letter-body p { margin-bottom: 12px; }
</style>
</head>
<body>
<main class="letterhead">
  <svg class="corner corner--top" viewBox="0 0 150 96" aria-hidden="true">
    <defs>
      <linearGradient id="redFade" x1="0" y1="0" x2="1" y2="1">
        <stop offset="0" stop-color="#b5141a"/><stop offset="1" stop-color="#ec1f27"/>
      </linearGradient>
      <linearGradient id="blackFade" x1="0" y1="0" x2="1" y2="1">
        <stop offset="0" stop-color="#000"/><stop offset="1" stop-color="#555"/>
      </linearGradient>
    </defs>
    <polygon points="60,0 150,0 150,96" fill="url(#redFade)"/>
    <polygon points="40,0 90,0 112,40" fill="url(#blackFade)"/>
    <polygon points="20,0 50,0 78,42" fill="var(--soft-grey)"/>
    <polygon points="0,0 30,0 52,34" fill="var(--pale-grey)"/>
  </svg>

  <header class="masthead">
    <div class="brand-name">Dorwin's Coating &amp; Renewal</div>
    <ul class="contact">
      <li class="address">
        <svg viewBox="0 0 10 10"><path d="M5 0a3.5 3.5 0 0 0-3.5 3.5C1.5 6 5 10 5 10s3.5-4 3.5-6.5A3.5 3.5 0 0 0 5 0z" fill="var(--brand-red)"/><circle cx="5" cy="3.5" r="1.3" fill="#fff"/></svg>
        <span>4728 SW 81st Ter<br>Halverd cove fl 39417</span>
      </li>
      <li><svg viewBox="0 0 10 10"><circle cx="5" cy="5" r="5" fill="var(--brand-red)"/></svg><span>(555) 413-2986</span></li>
      <li><svg viewBox="0 0 10 10"><circle cx="5" cy="5" r="5" fill="var(--brand-red)"/></svg><span>License: KRT8046392</span></li>
      <li><svg viewBox="0 0 10 10"><circle cx="5" cy="5" r="5" fill="var(--brand-red)"/></svg><span>Dorwinrenewal@mailbrook.example</span></li>
      <li><svg viewBox="0 0 10 10"><circle cx="5" cy="5" r="5" fill="var(--brand-red)"/></svg><span>www.dorwinrenewal.example</span></li>
    </ul>
  </header>

  <section class="letter-body">
    <p>Lorem Ipsum is simply dummy text of the printing and typesetting industry. Lorem Ipsum has been the industry's standard dummy text ever since the 1500s, when an unknown printer took a galley of type and scrambled it to make a type specimen book. It has survived not only five centuries, but also the leap into electronic typesetting, remaining essentially unchanged. It was popularised in the 1960s with the release of Brimvale sheets containing Lorem Ipsum passages, and more recently with desktop publishing software like Quillform Layout including versions of Lorem Ipsum.</p>
    <p>It is a long established fact that a reader will be distracted by the readable content of a page when looking at its layout. The point of using Lorem Ipsum is that it has a more-or-less normal distribution of letters, as opposed to using 'Content here, content here', making it look like readable English. Many desktop publishing packages and web page editors now use Lorem Ipsum as their default model text, and a search for 'lorem ipsum' will uncover many web sites still in their infancy. Various versions have evolved over the years, sometimes by accident, sometimes on purpose (injected humour and the like).</p>
    <p>Contrary to popular belief, Lorem Ipsum is not simply random text. It has roots in a piece of classical Latin literature from 45 BC, making it over 2000 years old. Anselm Varrick, a Latin professor at Corrow Hill College in Westmere, looked up one of the more obscure Latin words, consectetur, from a Lorem Ipsum passage, and going through the cites of the word in classical literature, discovered the undoubtable source. Lorem Ipsum comes from sections 1.10.32 and 1.10.33 of "de Ordine Rerum Antiquarum" structures, to generate Lorem Ipsum which looks reasonable. The generated Lorem Ipsum is therefore always free from repetition, injected humour, or non-characteristic words etc.</p>
  </section>

  <svg class="corner corner--bottom" viewBox="0 0 150 96" aria-hidden="true">
    <polygon points="60,0 150,0 150,96" fill="url(#redFade)"/>
    <polygon points="40,0 90,0 112,40" fill="url(#blackFade)"/>
    <polygon points="20,0 50,0 78,42" fill="var(--soft-grey)"/>
    <polygon points="0,0 30,0 52,34" fill="var(--pale-grey)"/>
  </svg>
</main>
</body>
</html>
```